Business Card Design for Marketing Firm

Looking for business card design for higher end marketing firm. Clean but impressionable/trendy. We are a marketing firm that represents manufacturers in the foodservice equipment and supply industry. Our customers are end users such has hotels, restaurants, country clubs, convention centers and casinos as well as distributors of restaurants supplies and equipment, and manufacturers of foodservice equipment and supplies.
Target Market(s)
Hotels, Restaurants, Supply & Equipment Distributors, Foodservice Manufacturers
Industry/Entity Type
Foodservice/Hospitality
Contact Information for Business Card
Name, Title, Contact Number, Email, Website, Social Media, Address
Requirements
Must have
- Clean & Simple but Serious and Impressionable

```html
<!DOCTYPE html>
<html lang="en">
<head>
<meta charset="utf-8">
<title>Meridian Hospitality Reps – Business Card</title>
<link href="https://fonts.googleapis.com/css2?family=Cinzel:wght@700&amp;family=Crimson+Text:wght@400;600&amp;display=swap" rel="stylesheet">
<style>
  :root {
    --navy: #2a2878;
    --white: #ffffff;
    --grey: #c4c4c6;
    --backdrop: #2b2b2d;
    --heading-font: "Cinzel", serif;
    --body-font: "Crimson Text", serif;
  }
  * { margin: 0; padding: 0; box-sizing: border-box; }
  html, body { width: 1200px; height: 900px; overflow: hidden; }
  body {
    background: var(--backdrop);
    display: flex;
    flex-direction: column;
    align-items: center;
    justify-content: center;
    gap: 60px;
  }
  .card {
    position: relative;
    width: 630px;
    height: 360px;
    border-radius: 22px;
    overflow: hidden;
  }
  .card-front { background: var(--white); }
  .card-back { background: var(--navy); }
  .wave { position: absolute; inset: 0; width: 100%; height: 100%; }

  .brand {
    position: absolute;
    display: flex;
    align-items: center;
    white-space: nowrap;
    font-family: var(--body-font);
    font-weight: 600;
    line-height: 1;
  }
  .brand-dot { flex: none; border-radius: 50%; }

  .card-front .brand { left: 50px; top: 62px; gap: 10px; color: var(--navy); font-size: 26px; }
  .card-front .brand-dot { width: 14px; height: 14px; background: var(--navy); }

  .card-back .brand {
    left: 50%; top: 50%;
    transform: translate(-50%, -50%);
    gap: 14px;
    color: var(--white);
    font-size: 40px;
  }
  .card-back .brand-dot { width: 20px; height: 20px; background: var(--white); }

  .contact {
    position: absolute;
    right: 30px;
    top: 206px;
    color: var(--white);
    font-family: var(--body-font);
    text-align: right;
  }
  .contact-name {
    font-family: var(--heading-font);
    font-weight: 700;
    font-size: 19px;
    letter-spacing: 0.04em;
    margin-right: 26px;
  }
  .contact-title { font-size: 15px; margin-right: 26px; margin-bottom: 2px; }
  .contact-line {
    display: flex;
    justify-content: flex-end;
    align-items: center;
    gap: 8px;
    font-size: 13.5px;
    line-height: 15.5px;
  }
  .contact-line .spacer { width: 18px; }
  .icon { width: 16px; height: 16px; flex: none; }
  .social { display: flex; gap: 5px; margin-right: 4px; }
  .social span { width: 12px; height: 12px; border-radius: 50%; background: var(--white); opacity: 0.85; }
</style>
</head>
<body>

<section class="card card-front" aria-label="Business card front">
  <svg class="wave" viewBox="0 0 630 360" preserveAspectRatio="none" aria-hidden="true">
    <path d="M0,95 C120,160 260,172 380,174 C480,176 570,178 630,190 L630,360 L0,360 Z" fill="var(--navy)"/>
    <path d="M0,103 C120,166 260,176 380,178 C480,180 570,182 630,194 L630,360 L0,360 Z" fill="var(--white)"/>
    <path d="M0,110 C110,164 250,178 370,180 C480,182 570,186 630,200 L630,360 L0,360 Z" fill="var(--grey)"/>
    <path d="M0,125 C120,176 260,182 380,182 C470,182 560,190 630,212 L630,360 L0,360 Z" fill="var(--navy)"/>
  </svg>

  <div class="brand">
    <span class="brand-dot" aria-hidden="true"></span>
    <span class="brand-name">Meridian Hospitality Reps</span>
  </div>

  <div class="contact">
    <div class="contact-name">DANIEL HARLOW</div>
    <div class="contact-title">Co-Founder</div>
    <div class="contact-line">P.O. Box 4021 LN-12<span class="spacer"></span></div>
    <div class="contact-line">Linden Ave 14, Fairview<span class="spacer"></span></div>
    <div class="contact-line">555-014-2790
      <svg class="icon" viewBox="0 0 16 16" aria-hidden="true"><path d="M4 2l2.5 3-1.5 1.5c.8 1.8 2.2 3.2 4 4L10.5 9 13.5 11.5 12 14C7 13.5 2.5 9 2 4z" fill="var(--white)"/></svg>
    </div>
    <div class="contact-line">info@meridianreps.com
      <svg class="icon" viewBox="0 0 16 16" aria-hidden="true"><rect x="1.5" y="3.5" width="13" height="9" fill="none" stroke="var(--white)" stroke-width="1.4"/><path d="M1.5 3.5L8 9l6.5-5.5" fill="none" stroke="var(--white)" stroke-width="1.4"/></svg>
    </div>
    <div class="contact-line">www.meridianreps.com
      <svg class="icon" viewBox="0 0 16 16" aria-hidden="true"><circle cx="8" cy="8" r="6.2" fill="none" stroke="var(--white)" stroke-width="1.3"/><ellipse cx="8" cy="8" rx="2.6" ry="6.2" fill="none" stroke="var(--white)" stroke-width="1.1"/><path d="M2 8h12" stroke="var(--white)" stroke-width="1.1"/></svg>
    </div>
    <div class="contact-line">@meridianreps
      <span class="social" aria-label="Social media"><span></span><span></span><span></span><span></span></span>
    </div>
  </div>
</section>

<section class="card card-back" aria-label="Business card back">
  <div class="brand">
    <span class="brand-dot" aria-hidden="true"></span>
    <span class="brand-name">Meridian Hospitality Reps</span>
  </div>
</section>

</body>
</html>
```